Business Card for a mobile physiotherapy company

I need a layout for a business card for a mobile physiotherapy company.
Slogan is "Mobile Physiotherapy - Your Road To Recovery"
Phone number is 867-555-0142
Email VardenTherapy@postnest.ca (subject to change with website)
Website www.VardenTherapy.ca
My name and credentials: Luke Varden Luke Varden, BSc(kin), MPT, CAFCI, IMS
Information maybe included: Direct Billing, Services including Physiotherapy, IMS, acupuncture
Maybe include facebook and instagram logos
One side with the logo clean and sharp
Other side with details, try not to look too busy, keep everything concise

```html
<!DOCTYPE html>
<html lang="en">
<head>
<meta charset="utf-8">
<title>Varden Therapy – Business Card</title>
<link href="https://fonts.googleapis.com/css2?family=Open+Sans:wght@400;600;700&display=swap" rel="stylesheet">
<style>
  :root {
    --stage: #2b2b2d;
    --green-top: #13695e;
    --green-bottom: #0c4d45;
    --navy: #2f4b7c;
    --green-text: #15604f;
    --ink: #4a4a4a;
    --white: #ffffff;
  }
  * { box-sizing: border-box; margin: 0; padding: 0; }
  html, body {
    width: 1200px; height: 892px; overflow: hidden;
    background: var(--stage);
    font-family: "Open Sans", Arial, sans-serif;
  }
  .canvas { position: relative; width: 1200px; height: 892px; }
  .card {
    position: absolute; width: 620px; height: 354px;
    border-radius: 2px;
    box-shadow: 0 14px 30px rgba(0,0,0,.45);
  }
  /* back side */
  .card-back {
    left: 60px; top: 60px;
    background: linear-gradient(160deg, var(--green-top), var(--green-bottom));
    color: var(--white);
    text-align: center;
  }
  .social {
    position: absolute; top: 22px; right: 24px; display: flex; gap: 6px;
  }
  .social span {
    width: 22px; height: 22px; border-radius: 50%; background: var(--white);
  }
  .back-brand {
    position: absolute; top: 112px; left: 0; right: 0;
    font-size: 46px; font-weight: 700; letter-spacing: 3px;
    text-transform: uppercase; line-height: 1;
  }
  .back-tagline {
    position: absolute; top: 246px; left: 0; right: 0;
    font-size: 16px; line-height: 1.35;
  }
  .back-tagline .dot { margin: 0 6px; }
  /* front side */
  .card-front {
    left: 520px; top: 478px;
    background: var(--white);
  }
  .front-brand {
    position: absolute; top: 40px; right: 40px;
    text-align: right; color: var(--navy);
    font-weight: 700; text-transform: uppercase; line-height: 1.05;
  }
  .front-brand .brand-main { font-size: 40px; letter-spacing: 3px; }
  .front-brand .brand-sub { font-size: 20px; letter-spacing: 10px; }
  .contact-block { position: absolute; left: 40px; bottom: 34px; }
  .person-name {
    color: var(--navy); font-size: 24px; font-weight: 700;
    text-transform: uppercase; line-height: 1.1;
  }
  .credentials { color: var(--navy); font-size: 15px; font-weight: 600; }
  .billing { color: var(--green-text); font-size: 15px; font-weight: 700; }
  .divider { width: 90px; height: 2px; background: var(--navy); margin: 8px 0 10px; }
  .contact-list { list-style: none; }
  .contact-list li {
    display: flex; align-items: center; gap: 12px;
    color: var(--ink); font-size: 15px; line-height: 1.55;
  }
  .contact-list svg { width: 15px; height: 15px; fill: var(--navy); flex: none; }
</style>
</head>
<body>
<main class="canvas">
  <section class="card card-back" aria-label="Card back">
    <div class="social" aria-label="Social profiles"><span></span><span></span></div>
    <div class="back-brand">Varden Therapy</div>
    <p class="back-tagline">
      Mobile Physiotherapy - Your Road To Recovery<br>
      Physiotherapy<span class="dot">•</span>IMS<span class="dot">•</span>Acupuncture
    </p>
  </section>

  <section class="card card-front" aria-label="Card front">
    <div class="front-brand">
      <div class="brand-main">Varden</div>
      <div class="brand-sub">Therapy</div>
    </div>
    <div class="contact-block">
      <h1 class="person-name">Luke Varden</h1>
      <p class="credentials">BSc(kin), MPT, CAFCI, IMS</p>
      <p class="billing">Direct Billing</p>
      <div class="divider"></div>
      <ul class="contact-list">
        <li>
          <svg viewBox="0 0 24 24" aria-hidden="true"><path d="M6.6 10.8a15 15 0 0 0 6.6 6.6l2.2-2.2c.3-.3.7-.4 1-.2 1.1.4 2.3.6 3.6.6.6 0 1 .4 1 1V20c0 .6-.4 1-1 1A17 17 0 0 1 3 4c0-.6.4-1 1-1h3.5c.6 0 1 .4 1 1 0 1.3.2 2.5.6 3.6.1.3 0 .7-.2 1z"/></svg>
          867-555-0142
        </li>
        <li>
          <svg viewBox="0 0 24 24" aria-hidden="true"><path d="M2 5h20v14H2zm2 2v.5l8 5 8-5V7l-8 5z"/></svg>
          VardenTherapy@postnest.ca
        </li>
        <li>
          <svg viewBox="0 0 24 24" aria-hidden="true"><path d="M12 2a10 10 0 1 0 0 20 10 10 0 0 0 0-20zm6.9 9h-3a15 15 0 0 0-1.3-6A8 8 0 0 1 18.9 11zM12 4c.9 1.2 1.7 3.9 1.9 7h-3.8c.2-3.1 1-5.8 1.9-7zM9.4 5a15 15 0 0 0-1.3 6h-3A8 8 0 0 1 9.4 5zM5.1 13h3a15 15 0 0 0 1.3 6A8 8 0 0 1 5.1 13zM12 20c-.9-1.2-1.7-3.9-1.9-7h3.8c-.2 3.1-1 5.8-1.9 7zm2.6-1a15 15 0 0 0 1.3-6h3a8 8 0 0 1-4.3 6z"/></svg>
          www.VardenTherapy.ca
        </li>
      </ul>
    </div>
  </section>
</main>
</body>
</html>
```